Re-design and craft the perfect CV platform

We are building a CV-based platform designed to connect employees and employers, with a strong focus on individual users. As we're just starting out, we're looking to have our platform and logo redesigned to better reflect our vision
https://app.zelvorhire.com/
Colors like in the logo attached
#87C032 #6A6E71 #618930 - also you can add more colors if you like.
https://app.zelvorhire.com/dashboard - This page would be nice if you plan it, like personal Bio dashboard. Attached picture (Dashboard wanted) one idea from how we would like to be, but we are open for new professional ideas/solutions.
https://app.zelvorhire.com/posts - On this page we want to be showed the jobs posted. Attached one picture about our idea (jobs page wanted)
https://app.zelvorhire.com/profile - design something nice.
Only Photoshop, Illustrator or Figma
Other pictures from the app attached (as looking right now)

Target Market(s)

Job seekers, HR, Recruiters

Industry/Entity Type

HR Tech

Number of Pages Required

5+ page

Colors
00AB8E
00BBA5
67D7C9
C6EFE9
E9F9F6

```html
<!DOCTYPE html>
<html lang="en">
<head>
<meta charset="utf-8">
<title>Zelvor Dashboard</title>
<link href="https://fonts.googleapis.com/css2?family=Poppins:wght@400;500;600;700&display=swap" rel="stylesheet">
<style>
:root{
  --green:#87C032;
  --green-dark:#618930;
  --grey:#6A6E71;
  --ink:#4a4d50;
  --panel:#f2f2f2;
  --line:#dcdcdc;
  --white:#ffffff;
  --track:#e2e2e2;
}
*{box-sizing:border-box;margin:0;padding:0}
html,body{width:1200px;height:712px;overflow:hidden;background:var(--white);font-family:"Poppins",sans-serif;color:var(--ink)}
.dashboard{position:relative;width:1200px;height:712px}
.abs{position:absolute}

/* sidebar */
.sidebar{left:0;top:0;width:224px;height:698px;background:var(--panel);border-radius:0 0 10px 0}
.brand{left:0;top:26px;width:224px;text-align:center}
.brand-mark{display:inline-block;width:30px;height:30px;border-radius:50%;background:var(--green)}
.brand-name{display:block;font-weight:700;font-size:20px;color:var(--green);letter-spacing:.5px;margin-top:4px}
.profile-photo{left:43px;top:110px;width:138px;height:137px;border-radius:10px;background:linear-gradient(160deg,#c9d3dc,#8f9aa5)}
.profile-name{left:0;top:254px;width:224px;text-align:center;font-weight:700;font-size:16px;color:var(--green)}
.profile-role{left:0;top:277px;width:224px;text-align:center;font-size:10px}
.profile-mail{left:0;top:290px;width:224px;text-align:center;font-size:13px;font-weight:500}
.divider{height:1px;background:var(--line)}
.facts{left:30px;top:340px;font-size:11px}
.facts dl{display:grid;grid-template-columns:62px 1fr;row-gap:7.5px;align-items:center;line-height:15px}
.facts dt{font-weight:600;color:var(--grey)}
.facts dd{font-size:8px}
.side-block{left:30px;font-size:11px}
.side-block h4{font-weight:600;color:var(--grey);font-size:11.5px}
.side-block p{font-size:8px;margin-top:3px}

/* header */
.topbar{left:224px;top:20px;width:958px;height:72px;background:var(--panel);border-radius:0 36px 36px 0}
.page-title{left:249px;top:44px;font-size:19px;font-weight:700;color:var(--grey)}
.nav{left:988px;top:48px;display:flex;gap:14px;font-size:11.5px;font-weight:600;color:var(--grey);align-items:center}
.nav .caret{color:var(--green);font-size:8px}
.bell{left:1079px;top:47px}
.avatar{left:1119px;top:31px;width:50px;height:50px;border-radius:50%;background:linear-gradient(160deg,#a8d46a,var(--green))}

/* about */
.about{left:241px;top:110px;width:701px;height:161px;background:var(--green);border-radius:12px;overflow:hidden;color:var(--white);padding:22px 30px}
.about h2{font-size:18.5px;font-weight:700;position:relative;z-index:1}
.about p{font-size:14.8px;line-height:22.5px;position:relative;z-index:1}
.about-decor{position:absolute;right:0;top:0;width:230px;height:161px;background:radial-gradient(circle at 85% 100%,rgba(255,255,255,.16),rgba(255,255,255,0) 70%)}

/* main card */
.main-card{left:241px;top:286px;width:701px;height:412px;background:var(--panel);border-radius:12px}
.sec-title{font-size:15px;font-weight:600;color:var(--grey)}
.txt{font-size:12.8px}
.txt b{font-weight:600;color:var(--grey)}
.edu li{list-style:none;font-size:12.8px;margin-top:4.8px;position:relative;padding-left:11px}
.edu b{font-weight:600;color:var(--grey)}
.edu li::before,.bullets li::before{content:"";position:absolute;left:0;top:8px;width:4px;height:4px;border-radius:50%;background:var(--green)}
.tabs{display:flex;font-size:12.8px;font-weight:500;color:var(--grey)}
.tabs span{padding:0 0 4px}
.tabs .active{color:var(--green);border-bottom:2px solid var(--green);padding:0 9px 4px}
.job-logo{width:48px;height:48px;border-radius:50%;background:var(--white);box-shadow:0 2px 6px rgba(0,0,0,.08);display:flex;align-items:center;justify-content:center}
.job-logo i{width:20px;height:20px;border-radius:50%}
.job-text{font-size:12.8px;line-height:19px}
.job-text b{font-weight:600;color:var(--grey)}
.btn{height:25px;border-radius:13px;font-size:8.5px;font-weight:700;color:var(--white);display:flex;align-items:center;justify-content:center;letter-spacing:.2px}
.btn-details{width:69px;background:var(--green)}
.btn-message{width:69px;background:var(--grey)}

/* right column */
.skills-card{left:955px;top:110px;width:227px;height:355px;background:var(--panel);border-radius:12px}
.lang-card{left:955px;top:476px;width:227px;height:166px;background:var(--panel);border-radius:12px}
.bullets{list-style:none;font-size:12px;line-height:13.5px}
.bullets li{position:relative;padding-left:11px;margin-bottom:9px}
.bullets li::before{top:5px}
.lang{left:979px;width:182px}
.lang-row{display:flex;justify-content:space-between;align-items:flex-end}
.lang-row b{font-weight:600;font-size:13px;color:var(--grey)}
.lang-row span{font-size:10.5px}
.bar{height:9px;border-radius:5px;background:var(--track);margin-top:5px;overflow:hidden}
.bar i{display:block;height:100%;background:var(--green);border-radius:5px}
</style>
</head>
<body>
<div class="dashboard">

  <aside class="abs sidebar"></aside>
  <div class="abs brand"><span class="brand-mark"></span><span class="brand-name">ZELVOR</span></div>
  <div class="abs profile-photo" role="img" aria-label="Profile photo of Daniel Marsh"></div>
  <div class="abs profile-name">DANIEL MARSH</div>
  <div class="abs profile-role">Software Engineer</div>
  <div class="abs profile-mail">hello@danmarsh.net</div>
  <div class="abs divider" style="left:17px;top:324px;width:191px"></div>
  <div class="abs facts">
    <dl>
      <dt>Phone:</dt><dd>+01 555-204-7731</dd>
      <dt>Email:</dt><dd>hello@danmarsh.net</dd>
      <dt>Age:</dt><dd>35</dd>
      <dt>Sex:</dt><dd>Mail</dd>
      <dt>Address:</dt><dd>Some goes address here</dd>
    </dl>
  </div>
  <div class="abs divider" style="left:17px;top:460px;width:191px"></div>
  <div class="abs side-block" style="top:475px"><h4>Highest level of education:</h4><p>Master's Degree in Computer Science</p></div>
  <div class="abs divider" style="left:17px;top:523px;width:191px"></div>
  <div class="abs side-block" style="top:538px"><h4>Work Experience:</h4><p>Years of Work Experience: 15+ years</p></div>

  <header class="abs topbar"></header>
  <h1 class="abs page-title">ZELVOR DASHBOARD</h1>
  <nav class="abs nav"><span>JOBS<span class="caret">&#9660;</span></span><span>CV</span></nav>
  <svg class="abs bell" width="16" height="18" viewBox="0 0 16 18" aria-label="Notifications">
    <path d="M8 2a5 5 0 0 0-5 5v4l-2 3h14l-2-3V7a5 5 0 0 0-5-5z" fill="#6A6E71"/>
    <path d="M6 15a2 2 0 0 0 4 0z" fill="#6A6E71"/>
    <circle cx="12.5" cy="3" r="3" fill="#e8453c"/>
  </svg>
  <div class="abs avatar" role="img" aria-label="Account avatar"></div>

  <section class="abs about">
    <div class="about-decor" role="img" aria-label="Soft decorative glow"></div>
    <h2>ABOUT ME</h2>
    <p>Experienced and adaptable software engineer with over 15 years in the tech industry. Skilled in developing innovative solutions for complex problems, with a focus on efficiency, user experience, and reliability. Known for strong teamwork, attention to detail, and a commitment to professional development.</p>
  </section>

  <section class="abs main-card"></section>
  <div class="abs sec-title" style="left:271px;top:308px">WORK EXPERIENCE</div>
  <div class="abs txt" style="left:271px;top:329px">Years of Work Experience: 15+ years</div>
  <div class="abs" style="left:517px;top:298px;width:1px;height:56px;background:var(--line)"></div>
  <div class="abs sec-title" style="left:538px;top:306px">DRIVER'S LICENSE</div>
  <div class="abs txt" style="left:539px;top:329px"><b>License Type:</b> Full, Class B (valid for cars and light vehicles)</div>
  <div class="abs divider" style="left:267px;top:366px;width:650px"></div>

  <div class="abs sec-title" style="left:271px;top:380px">EDUCATION</div>
  <ul class="abs edu" style="left:271px;top:397px">
    <li><b>Qualification:</b> Master’s in Computer Science</li>
    <li><b>Institution:</b> University of Technology, 2010</li>
    <li><b>Additional Certifications:</b> Certified Sprint Lead, Cloud IT Automation Certificate</li>
  </ul>
  <div class="abs divider" style="left:267px;top:484px;width:650px"></div>

  <div class="abs sec-title" style="left:271px;top:496px">MY JOBS</div>
  <div class="abs tabs" style="left:271px;top:526px"><span style="margin-right:18px">Saved Jobs</span><span class="active">Applied Jobs</span><span style="margin-left:16px">Archived Jobs</span></div>
  <div class="abs divider" style="left:267px;top:548px;width:650px"></div>

  <div class="abs job-logo" style="left:271px;top:562px"><i style="background:#2fa7c9"></i></div>
  <div class="abs job-text" style="left:329px;top:567px"><b>Data Analyst:</b> Applied on yesterday 25 dec<br>Seeking a data-driven analyst to interpret complex data sets</div>
  <div class="abs btn btn-details" style="left:769px;top:573px">DETAILS</div>
  <div class="abs btn btn-message" style="left:843px;top:573px">MESAGE</div>
  <div class="abs divider" style="left:267px;top:620px;width:650px"></div>

  <div class="abs job-logo" style="left:271px;top:631px"><i style="background:#e94e3c"></i></div>
  <div class="abs job-text" style="left:329px;top:637px"><b>Product Manager:</b> Applied on yesterday 25 dec<br>Looking for a seasoned software engineer with a knack for ...</div>
  <div class="abs btn btn-details" style="left:769px;top:642px">DETAILS</div>
  <div class="abs btn btn-message" style="left:843px;top:642px">MESAGE</div>

  <section class="abs skills-card"></section>
  <div class="abs sec-title" style="left:979px;top:132px">SKILLS</div>
  <ul class="abs bullets" style="left:979px;top:161px;width:190px">
    <li>Velo, Krait, Torus, SQL</li>
    <li>Quillet, Brisk, Nodex</li>
    <li>DataVault, Lumbase</li>
    <li>Taskboard, Kanflow, Planly</li>
    <li>Problem-solving, Team Leadership, Communication, Adaptability</li>
  </ul>
  <div class="abs divider" style="left:973px;top:314px;width:192px"></div>
  <div class="abs sec-title" style="left:979px;top:331px">HOBBIES &amp; INTERESTS</div>
  <ul class="abs bullets" style="left:979px;top:360px;width:190px">
    <li>Reading newspapers</li>
    <li>Playing music</li>
    <li>Watching sports</li>
    <li>Going go-karting</li>
  </ul>

  <section class="abs lang-card"></section>
  <div class="abs sec-title" style="left:979px;top:494px">LANGUAGES</div>
  <div class="abs lang" style="top:516px"><div class="lang-row"><b>Romanian:</b><span>65%</span></div><div class="bar"><i style="width:61%"></i></div></div>
  <div class="abs lang" style="top:553px"><div class="lang-row"><b>Hungarian:</b><span>100%</span></div><div class="bar"><i style="width:100%"></i></div></div>
  <div class="abs lang" style="top:590px"><div class="lang-row"><b>Romanian:</b><span>80%</span></div><div class="bar"><i style="width:78%"></i></div></div>

</div>
</body>
</html>
```